Business card por a urban DJ, up scale audience target

Need a sober design, modern, conservative colors but i can consider some options, y play rnb, hip hop, EDM and top40.

Business card for contact and personal info, double sided, use logo attrached please; im 42 so i need a card acording to my age an target audience.

Target Market(s)

Adult people, up scale audience

Industry/Entity Type

Music Download

Contact Information for Business Card

Cel (318) 4207265518 www.lumadrift.com

Requirements
Must have
• open mind
Nice to have
• open mind
Should not have
• DJ

```html
<!DOCTYPE html>
<html lang="en">
<head>
<meta charset="UTF-8">
<title>Lumadrift Business Card</title>
<link rel="stylesheet" href="https://fonts.googleapis.com/css2?family=Arimo:wght@400;700&display=swap">
<style>
  :root {
    --page-bg: #d9d7d3;
    --ink: #141414;
    --ink-soft: #3a3a3a;
    --white: #ffffff;
    --steel-light: #a9a9a9;
    --steel-mid: #8a8a8a;
    --steel-dark: #6a6a6a;
    --paper-light: #f6f6f6;
    --paper-shade: #c9c9c9;
    --contact-text: #f0f0f0;
  }
  * { box-sizing: border-box; margin: 0; padding: 0; }
  html, body {
    width: 1200px; height: 950px; overflow: hidden;
    background: var(--page-bg);
    font-family: "Arimo", Arial, sans-serif;
  }
  .sheet {
    width: 1200px; height: 950px;
    display: flex; flex-direction: column;
    align-items: center; justify-content: center; gap: 30px;
  }
  .card {
    position: relative;
    width: 760px; height: 434px;
    overflow: hidden;
    box-shadow: 0 10px 26px rgba(0,0,0,.28);
  }
  .card-art { position: absolute; inset: 0; width: 100%; height: 100%; display: block; }

  /* Front */
  .brand-name {
    position: absolute; left: 46px; top: 44px;
    font-weight: 700; font-size: 84px; letter-spacing: 2px;
    color: var(--white); line-height: 1;
  }
  .contact {
    position: absolute; right: 44px; bottom: 36px;
    text-align: right; color: var(--contact-text);
  }
  .contact-name { font-size: 24px; font-weight: 700; letter-spacing: 1px; }
  .contact-title { font-size: 17px; letter-spacing: 1px; margin-bottom: 10px; }
  .contact-line {
    display: flex; align-items: center; justify-content: flex-end; gap: 10px;
    font-size: 18px; margin-top: 6px;
  }
  .contact-line svg { width: 18px; height: 18px; flex: none; }

  /* Back */
  .back-content {
    position: absolute; inset: 0;
    display: flex; flex-direction: column; align-items: center; justify-content: center;
  }
  .back-brand {
    font-weight: 700; font-size: 104px; letter-spacing: 3px;
    color: var(--ink); line-height: 1;
  }
  .back-url {
    margin-top: 14px; font-size: 20px; letter-spacing: 4px; color: var(--ink-soft);
  }
</style>
</head>
<body>
<main class="sheet">

  <section class="card card-front" aria-label="Card front">
    <svg class="card-art" viewBox="0 0 760 434" preserveAspectRatio="none" aria-hidden="true">
      <defs>
        <linearGradient id="steel" x1="0" y1="0" x2="1" y2="1">
          <stop offset="0" stop-color="#b3b3b3"/>
          <stop offset="0.55" stop-color="#8e8e8e"/>
          <stop offset="1" stop-color="#686868"/>
        </linearGradient>
        <linearGradient id="gloss" x1="0" y1="0" x2="1" y2="0">
          <stop offset="0" stop-color="#121212"/>
          <stop offset="0.55" stop-color="#1d1d1d"/>
          <stop offset="1" stop-color="#5a5a5a"/>
        </linearGradient>
      </defs>
      <rect class="front-lower" width="760" height="434" fill="url(#steel)"/>
      <polygon class="front-upper" points="0,0 760,0 760,140 0,330" fill="url(#gloss)"/>
      <line class="front-divider" x1="0" y1="336" x2="760" y2="146" stroke="#ffffff" stroke-width="7"/>
    </svg>

    <div class="brand-name">LUMA</div>

    <div class="contact">
      <p class="contact-name">MARCUS VALE</p>
      <p class="contact-title">PRESIDENT</p>
      <p class="contact-line">
        <span>(318) 4207265518</span>
        <svg viewBox="0 0 18 18" aria-hidden="true"><rect x="5" y="1.5" width="8" height="15" rx="1.5" fill="none" stroke="currentColor" stroke-width="1.6"/><circle cx="9" cy="13.6" r="1" fill="currentColor"/></svg>
      </p>
      <p class="contact-line">
        <span>www.lumadrift.com</span>
        <svg viewBox="0 0 18 18" aria-hidden="true"><circle cx="9" cy="9" r="7.5" fill="none" stroke="currentColor" stroke-width="1.6"/><ellipse cx="9" cy="9" rx="3" ry="7.5" fill="none" stroke="currentColor" stroke-width="1.2"/><line x1="1.5" y1="9" x2="16.5" y2="9" stroke="currentColor" stroke-width="1.2"/></svg>
      </p>
    </div>
  </section>

  <section class="card card-back" aria-label="Card back">
    <svg class="card-art" viewBox="0 0 760 434" preserveAspectRatio="none" aria-hidden="true">
      <defs>
        <linearGradient id="paper" x1="0" y1="0" x2="1" y2="1">
          <stop offset="0" stop-color="#f7f7f7"/>
          <stop offset="0.6" stop-color="#e4e4e4"/>
          <stop offset="1" stop-color="#c4c4c4"/>
        </linearGradient>
      </defs>
      <rect width="760" height="434" fill="url(#paper)"/>
    </svg>
    <div class="back-content">
      <div class="back-brand">LUMA</div>
      <div class="back-url">LUMADRIFT.COM</div>
    </div>
  </section>

</main>
</body>
</html>
```